Small Business Broker Business Card Design

A business card design for a small business brokerage, which is a financial service, not unlike real estate brokerage, but for small businesses such as laundromats, pizza shops, restaurants, cleaners etc. The designs should all be simple, more conservative in nature, using the colors and font of the logo. Again, think real estate Brokerage as a business context
Contact Information for Business Card
Name: Glen R. Harlow. Title: Small Business Advisor. Email: g.harlow@bayfieldcapitalworks.example. Mobile: (555) 274-3918. Office: (555) 806-2147. www.bayfieldcapitalworks.example

```html
<!DOCTYPE html>
<html lang="en">
<head>
<meta charset="utf-8">
<title>Bayfield Capital Works – Business Card</title>
<link rel="stylesheet" href="https://fonts.googleapis.com/css2?family=Arimo:ital,wght@0,400;0,700;1,400;1,700&display=swap">
<style>
  :root {
    --navy: #172f5e;
    --navy-deep: #132852;
    --green: #7abd35;
    --white: #ffffff;
    --backdrop: #141414;
  }
  * { margin: 0; padding: 0; box-sizing: border-box; }
  html, body {
    width: 1200px; height: 963px; overflow: hidden;
    background: var(--backdrop);
  }
  .sheet {
    width: 1200px; height: 963px;
    display: flex; flex-direction: column; align-items: center; justify-content: center;
    gap: 40px;
  }
  .card {
    position: relative;
    width: 760px; height: 434px;
    border-radius: 22px;
    background: radial-gradient(circle at 65% 55%, #1b3668 0%, var(--navy) 45%, var(--navy-deep) 100%);
    overflow: hidden;
    color: var(--white);
    font-family: "Arimo", Arial, sans-serif;
  }

  /* Front */
  .holder { position: absolute; left: 58px; top: 52px; }
  .holder-name {
    font-style: italic; font-weight: 700;
    font-size: 34px; letter-spacing: 0.5px;
    text-transform: uppercase; color: var(--green);
  }
  .holder-title { font-style: italic; font-size: 20px; margin-top: 2px; }
  .contacts {
    position: absolute; left: 58px; top: 168px;
    list-style: none; font-size: 17px;
  }
  .contacts li { display: flex; align-items: center; gap: 10px; height: 26px; }
  .contacts svg { width: 16px; height: 16px; flex: none; }

  .brand { position: absolute; right: 40px; top: 178px; text-align: right; }
  .brand-name {
    font-weight: 700; font-size: 16px; letter-spacing: 1px;
    text-transform: uppercase;
    display: flex; align-items: center; justify-content: flex-end; gap: 8px;
  }
  .brand-mark { width: 10px; height: 10px; background: var(--green); }
  .brand-tagline { font-size: 12px; color: var(--white); opacity: 0.85; margin-top: 5px; }
  .swoosh { position: absolute; left: 0; top: 0; width: 760px; height: 434px; }

  /* Back */
  .card-back { display: flex; align-items: center; justify-content: center; }
  .lockup { text-align: center; }
  .lockup .brand-name { font-size: 30px; letter-spacing: 2px; gap: 14px; justify-content: center; }
  .lockup .brand-mark { width: 18px; height: 18px; }
  .lockup .brand-tagline { font-size: 16px; margin-top: 10px; }
</style>
</head>
<body>
<main class="sheet">

  <section class="card card-front">
    <svg class="swoosh" viewBox="0 0 760 434" aria-hidden="true">
      <polyline points="0,322 520,322 590,260 760,260" fill="none" stroke="var(--white)" stroke-width="12"/>
      <polyline points="0,342 528,342 598,280 760,280" fill="none" stroke="var(--green)" stroke-width="5"/>
    </svg>

    <header class="holder">
      <h1 class="holder-name">Glen R. Harlow</h1>
      <p class="holder-title">Small Business Advisor</p>
    </header>

    <ul class="contacts">
      <li>
        <svg viewBox="0 0 16 16"><path d="M4 1.5l2.5 3-1.4 1.6c.8 1.9 2.4 3.5 4.3 4.3l1.6-1.4 3 2.5-1.5 2.3C8 14 2 8 1.7 3z" fill="none" stroke="var(--green)" stroke-width="1.4" stroke-linejoin="round"/></svg>
        <span>(555) 806-2147</span>
      </li>
      <li>
        <svg viewBox="0 0 16 16"><rect x="4" y="1" width="8" height="14" rx="1.5" fill="none" stroke="var(--green)" stroke-width="1.4"/><line x1="7" y1="12.5" x2="9" y2="12.5" stroke="var(--green)" stroke-width="1.4"/></svg>
        <span>(555) 274-3918</span>
      </li>
      <li>
        <svg viewBox="0 0 16 16"><rect x="1" y="3" width="14" height="10" fill="none" stroke="var(--green)" stroke-width="1.4"/><polyline points="1,3 8,9 15,3" fill="none" stroke="var(--green)" stroke-width="1.4"/></svg>
        <span>g.harlow@bayfieldcapitalworks.example</span>
      </li>
      <li>
        <svg viewBox="0 0 16 16"><circle cx="8" cy="8" r="6.5" fill="none" stroke="var(--green)" stroke-width="1.3"/><ellipse cx="8" cy="8" rx="3" ry="6.5" fill="none" stroke="var(--green)" stroke-width="1.1"/><line x1="1.5" y1="8" x2="14.5" y2="8" stroke="var(--green)" stroke-width="1.1"/></svg>
        <span>www.bayfieldcapitalworks.example</span>
      </li>
    </ul>

    <div class="brand">
      <p class="brand-name"><span class="brand-mark"></span>Bayfield Capital Works, Inc</p>
      <p class="brand-tagline">Trusted guidance for Main Street owners</p>
    </div>
  </section>

  <section class="card card-back">
    <div class="lockup">
      <p class="brand-name"><span class="brand-mark"></span>Bayfield Capital Works, Inc</p>
      <p class="brand-tagline">Trusted guidance for Main Street owners</p>
    </div>
  </section>

</main>
</body>
</html>
```